needing web design for aerial and satellite installation comapny

We need our website designing, it needs to be professional and look creative,
We are a aerial and satellite company called Corvid Mend & Reach ()
I like this site design also some of the following maybe:

https://www.skylorn.co.uk/

http://brimwell.co.uk/

http://quillon4guard.co.uk/portfolio/kmt-brimwell/

The design will require coding once the design is complete, i haven't paid for this yet as i want to be sure the design is good before i commit.

The template needs to look professional and look like one of the leading companies.
The site will consist of all the features this site has https://www.skylorn.co.uk/

I like a modern design with the latest technology.

Target Market(s)

tv aerial satellite installation

Industry/Entity Type

Satellite Tv

Number of Pages Required

3 page

Font styles to use
Sans Serif

Colors

Designer to choose colors to be used in the design.

Requirements
Must have
• eb Contest Brief We need our website designing, it needs to be professional and look creative,
• We are a aerial and satellite company called Corvid Mend Reach ()
• I like this site design also some of the following maybe:
• https://www.skylorn.co.uk/
• http://brimwell.co.uk/
• http://quillon4guard.co.uk/portfolio/kmt-brimwell/
• The design will require coding once the design is complete, i haven't paid for this yet as i want to be sure the design is good before i commit.
• The template needs to look professional and look like one of the leading companies.
• The site will consist of all the features this site has https://www.skylorn.co.uk/
• I like a modern design with the latest technology.
Nice to have
• http://brimwell.co.uk/
Should not have
• poor design

```html
<!DOCTYPE html>
<html lang="en">
<head>
<meta charset="utf-8">
<title>Corvid Mend &amp; Reach — TV Aerial &amp; Satellite Installers</title>
<link href="https://fonts.googleapis.com/css2?family=Roboto+Condensed:wght@400;700&family=Roboto:wght@400;500;700&display=swap" rel="stylesheet">
<style>
:root{
  --orange:#e2582a;
  --blue:#1d4aa0;
  --navy:#2c3142;
  --ink:#1e2331;
  --white:#ffffff;
  --muted:#8a8f9e;
  --space-deep:#07090d;
  --space-mid:#16262b;
}
*{margin:0;padding:0;box-sizing:border-box}
html,body{width:1200px;height:2723px;overflow:hidden;background:#fff}
body{font-family:"Roboto",Arial,sans-serif;color:var(--ink);position:relative}
.cond{font-family:"Roboto Condensed","Arial Narrow",sans-serif}
section,header,footer,nav{position:absolute;left:0;width:1200px}

/* hero */
.hero{top:0;height:528px;overflow:hidden}
.hero-photo{position:absolute;inset:0;background:radial-gradient(ellipse 420px 380px at 1110px 420px,#3d6f8e 0%,#1c3b4e 45%,transparent 75%),radial-gradient(circle 40px at 1060px 80px,#7b8683,transparent 100%),linear-gradient(100deg,var(--space-deep) 0%,#0d1416 50%,var(--space-mid) 100%)}
.brand{position:absolute;display:flex;align-items:center;gap:12px}
.brand-mark{width:22px;height:22px;background:var(--white)}
.brand-name{font-family:"Roboto Condensed","Arial Narrow",sans-serif;font-weight:700;color:var(--white);letter-spacing:4px;font-size:15px;white-space:nowrap}
.hero .brand{left:160px;top:98px}
.hero-title{position:absolute;left:158px;top:240px;color:var(--orange);font-family:"Roboto Condensed","Arial Narrow",sans-serif;font-weight:700;font-size:60px;line-height:78px;text-transform:uppercase}
.hero-rule{position:absolute;height:7px;background:var(--white)}

/* nav */
.main-nav{top:528px;height:49px;background:#fff;border-bottom:1px solid #e4e4e4}
.main-nav ul{list-style:none;position:absolute;left:160px;top:0;display:flex;gap:22px;height:49px;align-items:center}
.main-nav li{font-family:"Roboto Condensed","Arial Narrow",sans-serif;font-weight:700;font-size:13px;color:var(--ink);text-transform:uppercase}
.nav-tools{position:absolute;left:752px;top:16px;display:flex;gap:20px;align-items:center}
.social-sq{width:15px;height:15px;border-radius:2px}
.lang{position:absolute;left:910px;top:0;width:130px;height:49px;background:#1b1b1f;color:#fff;font-family:"Roboto Condensed","Arial Narrow",sans-serif;font-weight:700;font-size:12px;display:flex;align-items:center;justify-content:center;gap:14px}

/* services */
.services{top:577px;height:438px;background:var(--orange);color:#fff;text-align:center}
.services h2{position:absolute;top:64px;left:0;width:100%;font-family:"Roboto Condensed","Arial Narrow",sans-serif;font-weight:700;font-size:35px;line-height:44px;text-transform:uppercase}
.services p{position:absolute;top:183px;left:170px;width:860px;font-size:12px;line-height:20px}
.service{position:absolute;top:288px;width:150px;margin-left:-75px;text-align:center}
.service svg{display:block;margin:0 auto 14px}
.service span{font-family:"Roboto Condensed","Arial Narrow",sans-serif;font-weight:700;font-size:13px;text-transform:uppercase}

/* slider */
.slider{top:1015px;height:455px;background:#fff}
.slide-side{position:absolute;top:0;height:455px;width:192px}
.slide-left{left:0;background:linear-gradient(90deg,#3a3733,#6d655c)}
.slide-right{left:1008px;background:linear-gradient(90deg,#8c8f94,#5a5d62)}
.slide-main{position:absolute;left:195px;top:0;width:810px;height:455px;background:radial-gradient(ellipse 260px 200px at 370px 240px,#f6dc8a 0%,#d7963c 30%,#3c5d7c 60%,#101823 100%)}
.slide-title{position:absolute;left:228px;top:283px;color:#fff;font-family:"Roboto Condensed","Arial Narrow",sans-serif;font-weight:700;font-size:48px;text-transform:uppercase;white-space:nowrap}
.slide-btn{position:absolute;left:228px;top:355px;width:185px;height:40px;border:2px solid #fff;color:#fff;font-family:"Roboto Condensed","Arial Narrow",sans-serif;font-weight:700;font-size:12px;display:flex;align-items:center}
.slide-btn span{padding-left:14px;flex:1}
.slide-btn i{width:44px;height:100%;border-left:2px solid #fff;display:flex;align-items:center;justify-content:center}
.slide-arrow{position:absolute;top:210px;width:38px;height:38px;border:2px solid #fff;background:rgba(0,0,0,.25);display:flex;align-items:center;justify-content:center}
.cam{position:absolute;left:227px;top:55px;width:30px;height:30px;border-radius:50%;background:var(--orange);display:flex;align-items:center;justify-content:center}

/* contact */
.contact{top:1470px;height:385px;background:var(--blue);color:#fff}
.contact h2{position:absolute;top:75px;width:100%;text-align:center;font-family:"Roboto Condensed","Arial Narrow",sans-serif;font-weight:700;font-size:32px;text-transform:uppercase}
.contact .rule{position:absolute;left:488px;top:127px;width:224px;height:8px;background:var(--orange)}
.contact p{position:absolute;top:158px;width:100%;text-align:center;font-size:17px;font-weight:500}
.contact .brand{left:160px;top:235px}
.phone-box{position:absolute;top:238px;width:272px;height:67px;border:2px solid #fff;display:flex;align-items:center;justify-content:center;font-family:"Roboto Condensed","Arial Narrow",sans-serif;font-weight:700;font-size:18px}

/* trust */
.trust{top:1855px;height:593px;background:#fff}
.trust h2{position:absolute;left:160px;top:50px;font-family:"Roboto Condensed","Arial Narrow",sans-serif;font-weight:700;font-size:34px;text-transform:uppercase;color:var(--ink)}
.trust .rule{position:absolute;left:160px;top:108px;width:90px;height:7px;background:var(--orange)}
.card{position:absolute;top:165px;width:268px}
.card-photo{height:177px}
.card h3{margin-top:15px;font-family:"Roboto Condensed","Arial Narrow",sans-serif;font-weight:700;font-size:17px;line-height:22px;color:var(--ink)}
.card p{margin-top:12px;font-size:11.5px;line-height:18px;color:#555a66}
.card a{display:block;margin-top:14px;font-family:"Roboto Condensed","Arial Narrow",sans-serif;font-weight:700;font-size:10px;color:var(--ink);text-decoration:none}
.divider{position:absolute;top:165px;width:3px;height:338px;background:var(--orange)}

/* footer */
.site-footer{top:2448px;height:275px;background:var(--navy);color:#fff}
.site-footer .brand{left:160px;top:45px}
.foot-info{position:absolute;left:160px;top:125px;font-size:10.5px;line-height:17px;color:var(--muted)}
.foot-copy{position:absolute;left:160px;top:212px;font-size:10px;color:var(--muted)}
.foot-rule{position:absolute;top:58px;width:3px;height:165px;background:var(--orange)}
.foot-nav{position:absolute;left:560px;top:63px;list-style:none}
.foot-nav li{font-family:"Roboto Condensed","Arial Narrow",sans-serif;font-weight:700;font-size:11.5px;line-height:22px;text-transform:uppercase}
.foot-label{position:absolute;left:800px;font-family:"Roboto Condensed","Arial Narrow",sans-serif;font-weight:700;font-size:11.5px;text-transform:uppercase}
.foot-social{position:absolute;left:890px;top:62px;display:flex;gap:10px}
.foot-social span{width:17px;height:17px;background:#6b6f7c}
.email-field{position:absolute;left:800px;top:138px;width:240px;height:30px;border:1px solid #c9ccd4;font-size:10px;font-style:italic;padding:8px 12px;color:#fff}
.submit{position:absolute;left:800px;top:168px;width:240px;height:30px;background:var(--orange);font-family:"Roboto Condensed","Arial Narrow",sans-serif;font-weight:700;font-size:11px;display:flex;align-items:center;justify-content:center}
</style>
</head>
<body>

<header class="hero">
  <div class="hero-photo" role="img" aria-label="Satellite orbiting above the Earth and moon in deep space"></div>
  <div class="brand"><span class="brand-mark"></span><span class="brand-name">CORVID MEND &amp; REACH</span></div>
  <h1 class="hero-title">Corvid Mend<br>&amp; Reach</h1>
  <div class="hero-rule" style="left:160px;top:312px;width:465px"></div>
  <div class="hero-rule" style="left:160px;top:390px;width:285px"></div>
</header>

<nav class="main-nav">
  <ul>
    <li>Home</li><li>TV Aerial Services</li><li>Orbit Satellite TV</li><li>Smart Home</li><li>CCTV &amp; Alarm</li>
  </ul>
  <div class="nav-tools">
    <svg width="15" height="15" viewBox="0 0 16 16"><circle cx="6.5" cy="6.5" r="4.5" fill="none" stroke="#1e2331" stroke-width="2"/><line x1="10" y1="10" x2="14.5" y2="14.5" stroke="#1e2331" stroke-width="2"/></svg>
    <span class="social-sq" style="background:#3b5a9a"></span>
    <span class="social-sq" style="background:#41a8d8"></span>
    <span class="social-sq" style="background:#c9a25a"></span>
  </div>
  <div class="lang">LANGUAGE <svg width="8" height="5" viewBox="0 0 8 5"><path d="M0 0h8L4 5z" fill="#fff"/></svg></div>
</nav>

<section class="services">
  <h2>Smart Home TV Aerial &amp;<br>Satellite Installers</h2>
  <p>Lorem ipsum dolor sit amet, consectetur adipiscing elit, sed do eiusmod tempor incididunt ut labore et dolore magna aliqua. Ut enim ad minim veniam, quis nostrud exercitation ullamco laboris nisi ut aliquip ex ea commodo consequat.Lorem ipsum dolor sit amet, consectetur adipiscing elit, sed do eiusmod tempor incididunt ut labore et dolore magna aliqua. Ut enim ad minim veniam, quis nostrud exercitation ullamco laboris nisi ut aliquip ex ea commodo consequat.</p>

  <div class="service" style="left:218px">
    <svg width="40" height="40" viewBox="0 0 40 40" fill="none" stroke="#fff" stroke-width="2.5"><rect x="5" y="12" width="30" height="21" rx="2"/><path d="M14 5l6 7 6-7"/><line x1="29" y1="18" x2="29" y2="27"/></svg>
    <span>TV Aerial Service</span>
  </div>
  <div class="service" style="left:377px">
    <svg width="40" height="40" viewBox="0 0 40 40" fill="none" stroke="#fff" stroke-width="2.5"><path d="M8 14a14 14 0 0 0 18 18z" fill="#fff"/><line x1="17" y1="23" x2="30" y2="10"/><line x1="12" y1="30" x2="8" y2="37"/><line x1="18" y1="31" x2="22" y2="37"/></svg>
    <span>Orbit Satellite TV</span>
  </div>
  <div class="service" style="left:522px">
    <svg width="40" height="40" viewBox="0 0 40 40" fill="none" stroke="#fff" stroke-width="2.5"><rect x="4" y="8" width="32" height="24" rx="3"/><circle cx="14" cy="20" r="5"/><rect x="23" y="14" width="8" height="12"/></svg>
    <span>Sound &amp; Vision</span>
  </div>
  <div class="service" style="left:678px">
    <svg width="40" height="40" viewBox="0 0 40 40" fill="none" stroke="#fff" stroke-width="2.5"><path d="M5 19L20 6l15 13v15H5z"/><path d="M14 22a8 8 0 0 1 12 0M17 26a4 4 0 0 1 6 0"/></svg>
    <span>Smart Home System</span>
  </div>
  <div class="service" style="left:830px">
    <svg width="40" height="40" viewBox="0 0 40 40" fill="none" stroke="#fff" stroke-width="3"><path d="M5 16a21 21 0 0 1 30 0M10 22a13 13 0 0 1 20 0M15 28a6 6 0 0 1 10 0"/><circle cx="20" cy="33" r="1.5" fill="#fff"/></svg>
    <span>Wi-Fi Solution</span>
  </div>
  <div class="service" style="left:977px">
    <svg width="40" height="40" viewBox="0 0 40 40" fill="none" stroke="#fff" stroke-width="2.5"><path d="M7 22L20 11l13 11"/><rect x="11" y="24" width="18" height="10" fill="#fff"/><path d="M14 8a9 9 0 0 1 12 0"/></svg>
    <span>Communal TV Sys.</span>
  </div>
</section>

<section class="slider">
  <div class="slide-side slide-left" role="img" aria-label="Engineer holding cables"></div>
  <div class="slide-side slide-right" role="img" aria-label="Satellite dish mounted on a roof"></div>
  <div class="slide-main" role="img" aria-label="Man relaxing in a chair with a remote in front of a large bright TV screen"></div>
  <div class="cam"><svg width="16" height="11" viewBox="0 0 16 11"><rect width="11" height="11" rx="2" fill="#fff"/><path d="M11 4l5-3v9l-5-3z" fill="#fff"/></svg></div>
  <div class="slide-title">Why Use Corvid Mend &amp; Reach</div>
  <div class="slide-btn"><span>OUR SERVICES</span><i><svg width="7" height="10" viewBox="0 0 7 10"><path d="M0 0l7 5-7 5z" fill="#fff"/></svg></i></div>
  <div class="slide-arrow" style="left:80px"><svg width="7" height="10" viewBox="0 0 7 10"><path d="M7 0L0 5l7 5z" fill="#fff"/></svg></div>
  <div class="slide-arrow" style="left:1083px"><svg width="7" height="10" viewBox="0 0 7 10"><path d="M0 0l7 5-7 5z" fill="#fff"/></svg></div>
</section>

<section class="contact">
  <h2>Contact Corvid Mend &amp; Reach Today - For Same Day Service</h2>
  <div class="rule"></div>
  <p>Lorem ipsum dolor sit amet, consectetur adipiscing elit, sed do eiusmod tempor</p>
  <div class="brand"><span class="brand-mark"></span><span class="brand-name">CORVID MEND &amp; REACH</span></div>
  <div class="phone-box" style="left:430px">Free Phone : 01 2345 6789</div>
  <div class="phone-box" style="left:733px">Mobile No : 01 2345 6789</div>
</section>

<section class="trust">
  <h2>Trust &amp; Reliability</h2>
  <div class="rule"></div>

  <article class="card" style="left:160px">
    <div class="card-photo" role="img" aria-label="Man watching a large bright TV screen" style="background:radial-gradient(ellipse 110px 80px at 110px 90px,#f3d484,#c98a3a 40%,#2f4a66 75%,#111a25)"></div>
    <h3>Same Day TV Aerial<br>Installations</h3>
    <p>Lorem ipsum dolor sit amet, consectetur adipiscing elit,sed do eiusmod tempor incididunt ut labore et dolore magna aliqua.Ut enim ad minim veniam,</p>
    <a>LEARN MORE</a>
  </article>
  <div class="divider" style="left:444px"></div>

  <article class="card" style="left:461px">
    <div class="card-photo" role="img" aria-label="Engineer working on cables beside a wall socket panel" style="background:linear-gradient(90deg,#4a3f36,#8a7a68 55%,#1f1f22 75%,#3a3a3d)"></div>
    <h3>Local Friendly &amp;<br>Qualified Engineers</h3>
    <p>Lorem ipsum dolor sit amet, consectetur adipiscing elit,sed do eiusmod tempor incididunt ut labore et dolore magna aliqua.Ut enim ad minim veniam,</p>
    <a>LEARN MORE</a>
  </article>
  <div class="divider" style="left:745px"></div>

  <article class="card" style="left:762px">
    <div class="card-photo" role="img" aria-label="Satellite dish mounted on a tiled roof" style="background:linear-gradient(135deg,#9a8f86,#c7c8cc 45%,#7a5a4a)"></div>
    <h3>Free No Obligation<br>Estimates</h3>
    <p>Lorem ipsum dolor sit amet, consectetur adipiscing elit,sed do eiusmod tempor incididunt ut labore et dolore magna aliqua.Ut enim ad minim veniam,</p>
    <a>LEARN MORE</a>
  </article>
</section>

<footer class="site-footer">
  <div class="brand"><span class="brand-mark"></span><span class="brand-name">CORVID MEND &amp; REACH</span></div>
  <div class="foot-info">Lorem Ipsum Dolor Sit Amet<br>Connectetur Amet Lorem<br>0012 345 6789<br>info@corvidmendandreach.com</div>
  <div class="foot-copy">© Copyright 2018 Corvid Mend And Reach, All Rights Reserved.</div>

  <div class="foot-rule" style="left:543px"></div>
  <ul class="foot-nav">
    <li>Home</li><li>TV Aerial Services</li><li>Orbit Satellite TV</li><li>Smart Home</li><li>CCTV &amp; Alarm</li>
  </ul>

  <div class="foot-rule" style="left:780px"></div>
  <div class="foot-label" style="top:65px">Connect</div>
  <div class="foot-social"><span></span><span></span><span></span></div>
  <div class="foot-label" style="top:115px">Subscribe</div>
  <div class="email-field">Enter Your Email</div>
  <div class="submit">SUBMIT</div>
</footer>

</body>
</html>
```